Beacon Advisory Website

I currently have a website www.beaconadvisoryinc.com. We are a IT Consulting Company. Our website will pretty much tell out our services. I am looking to enhance my website and make it look more professional. Looking for very classy and Contemporary look and design for my website.

It Company

```html
<!DOCTYPE html>
<html lang="en">
<head>
<meta charset="utf-8">
<title>Beacon Advisory – IT Consulting</title>
<link href="https://fonts.googleapis.com/css2?family=Lato:wght@400;700&family=Montserrat:wght@700;800&display=swap" rel="stylesheet">
<style>
:root{
  --blue:#0aa0dc;
  --blue-deep:#078fc6;
  --navy:#1b3f7a;
  --ink:#333;
  --muted:#8a8a8a;
  --soft:#f1f1f1;
  --band:#efefef;
  --dark:#1e1e1e;
  --darker:#111;
  --white:#fff;
}
*{margin:0;padding:0;box-sizing:border-box}
html,body{width:1200px;height:3114px;overflow:hidden}
body{position:relative;font-family:'Lato',sans-serif;color:var(--ink);background:var(--white)}
.abs{position:absolute}
.center{text-align:center}

/* top bar */
.topbar{left:0;top:0;width:1200px;height:42px;background:#000}
.social{top:0;height:42px;display:flex}
.social span{width:40px;height:42px;background:#222;margin-right:2px;display:block}
.social span:first-child{margin-left:76px}
.phone{right:78px;top:0;height:42px;display:flex;align-items:center;gap:10px;color:#fff;font-size:14px}

/* header */
.header{left:0;top:42px;width:1200px;height:104px;background:#fff}
.brand{left:80px;top:30px;display:flex;align-items:center;gap:12px;color:var(--navy);font-family:'Montserrat',sans-serif;font-weight:800;font-size:26px;letter-spacing:1px}
.brand i{width:40px;height:40px;border-radius:50%;background:var(--navy);display:block}
.nav{left:490px;top:0;height:104px;display:flex}
.nav a{display:flex;align-items:center;height:104px;padding:0 28px;font-size:14px;color:#777;text-decoration:none}
.nav a.active{background:var(--blue);color:#fff;width:100px;justify-content:center;padding:0}

/* hero */
.hero{left:0;top:146px;width:1200px;height:522px;background:linear-gradient(160deg,#5b6570,#2e343b 55%,#3d4651)}
.hero-name{left:0;width:1200px;top:262px;color:#fff;font-family:'Lato',sans-serif;font-weight:700;font-size:34px;letter-spacing:2px}
.hero-tag{left:250px;width:700px;top:394px;color:#fff;font-size:20px;line-height:31px}
.btn-ghost{left:496px;top:506px;width:208px;height:52px;border:2px solid #fff;color:#fff;font-size:15px;display:flex;align-items:center;justify-content:center}
.arrow{top:361px;width:52px;height:52px;border:2px solid #fff;background:rgba(0,0,0,.35);color:#fff;font-size:30px;display:flex;align-items:center;justify-content:center;font-weight:700}

/* tiles */
.tile{top:668px;width:398px;height:208px;color:#fff}
.tile .photo{position:absolute;inset:0;background:linear-gradient(135deg,#8b9096,#5a5f66)}
.tile .shade{position:absolute;inset:0;background:rgba(40,40,40,.45)}
.tile .ico{position:absolute;left:44px;top:52px}
.tile h3{position:absolute;left:106px;top:52px;font-size:20px;font-weight:400}
.tile p{position:absolute;left:106px;top:88px;width:250px;font-size:13px;line-height:20px}

/* about */
.about-photo{left:176px;top:930px;width:270px;height:405px;background:linear-gradient(180deg,#e9e9e9,#2a2c33 60%)}
.about-title{left:490px;top:962px;font-family:'Montserrat',sans-serif;font-weight:800;font-size:31px;color:var(--blue);letter-spacing:1px}
.about-text{left:490px;top:1030px;width:560px;font-size:15px;line-height:31px;color:var(--muted)}
.btn-solid{left:488px;top:1212px;width:172px;height:56px;background:var(--blue);color:#fff;font-family:'Montserrat',sans-serif;font-weight:700;font-size:14px;display:flex;align-items:center;justify-content:center}

/* offer strip */
.offers{left:0;top:1335px;width:1200px;height:367px;background:var(--soft)}
.offer{top:1390px;width:260px}
.offer h4{font-size:20px;font-weight:400;margin-top:24px;line-height:22px;color:var(--ink)}
.offer p{font-size:13px;line-height:21px;color:var(--muted);margin-top:14px}
.offer a{display:block;margin-top:16px;font-size:14px;color:var(--navy);text-decoration:none}

/* services */
.sec-title{left:0;width:1200px;top:1757px;font-family:'Montserrat',sans-serif;font-weight:800;font-size:31px;color:var(--blue);letter-spacing:1px}
.sec-intro{left:200px;width:800px;top:1826px;font-size:14px;line-height:26px;color:#555}
.services{left:0;top:1945px;width:1200px;height:314px;background:var(--band)}
.service{top:1945px;width:300px;height:314px;padding:60px 34px 0}
.service.featured{background:#fff;box-shadow:0 0 12px rgba(0,0,0,.2)}
.service h5{font-size:22px;font-weight:400;margin-top:24px;color:var(--ink)}
.service p{font-size:13px;line-height:21px;color:var(--muted);margin-top:12px}

/* banner */
.banner{left:0;top:2321px;width:1200px;height:312px;background:linear-gradient(90deg,#dfe6ed,#c5d0db 40%,#eef1f4)}
.banner-veil{left:0;top:2321px;width:1200px;height:312px;background:rgba(255,255,255,.45)}
.banner-quote{left:280px;width:640px;top:2430px;font-size:22px;line-height:32px;color:#222}

/* newsletter */
.news-left{left:0;top:2633px;width:600px;height:103px;background:var(--blue)}
.news-right{left:600px;top:2633px;width:600px;height:103px;background:var(--blue-deep)}
.news-title{left:300px;width:300px;top:2665px;color:#fff;font-family:'Montserrat',sans-serif;font-weight:800;font-size:31px;letter-spacing:1px}
.news-input{left:648px;top:2666px;width:477px;height:36px;border:1.5px solid #fff;color:#fff;font-size:12px;display:flex;align-items:center;padding-left:12px}
.news-send{right:0;top:0;width:46px;height:33px;border-left:1.5px solid #fff;display:flex;align-items:center;justify-content:center;position:absolute}

/* footer */
.footer{left:0;top:2736px;width:1200px;height:316px;background:var(--dark)}
.footer-title{left:0;width:1200px;top:2795px;color:#fff;font-family:'Montserrat',sans-serif;font-weight:800;font-size:31px;letter-spacing:1px}
.office{top:2878px;color:#fff}
.office h6{display:flex;align-items:center;gap:14px;font-size:25px;font-weight:400}
.office p{margin:14px 0 0 52px;font-size:14px;line-height:21px}
.divider{top:2900px;width:1px;height:110px;background:#3a3a3a}
.copyright{left:0;top:3052px;width:1200px;height:62px;background:var(--darker);color:#666;font-size:14px;display:flex;align-items:center;justify-content:center}
.copyright b{color:var(--blue);font-weight:400;margin:0 6px}
</style>
</head>
<body>

<div class="abs topbar"></div>
<div class="abs social"><span></span><span></span><span></span></div>
<div class="abs phone">
  <svg width="18" height="18" viewBox="0 0 24 24" fill="none" stroke="#fff" stroke-width="2"><path d="M5 3h4l2 5-3 2a12 12 0 0 0 6 6l2-3 5 2v4a2 2 0 0 1-2 2A18 18 0 0 1 3 5a2 2 0 0 1 2-2z"/></svg>
  +1 (555) 014 2290
</div>

<header class="abs header">
  <div class="abs brand"><i></i>BEACON ADVISORY</div>
  <nav class="abs nav">
    <a class="active">Home</a><a>About Us</a><a>Services</a><a>Solutions</a><a>Career</a><a>Contact Us</a>
  </nav>
</header>

<section class="abs hero" role="img" aria-label="Team of business people joining hands in the middle"></section>
<div class="abs hero-name center">BEACON ADVISORY</div>
<p class="abs hero-tag center">Effective integration of information technology into an organization's business processes has become increasingly crucial to prosperity</p>
<div class="abs btn-ghost">READ MORE</div>
<div class="abs arrow" style="left:25px">«</div>
<div class="abs arrow" style="left:1122px">»</div>

<div class="abs tile" style="left:0">
  <div class="photo" role="img" aria-label="Consultants meeting in an office"></div><div class="shade"></div>
  <svg class="ico" width="40" height="40" viewBox="0 0 40 40" fill="none" stroke="#fff" stroke-width="2.5"><circle cx="20" cy="16" r="11"/><path d="M15 28h10M16 33h8"/></svg>
  <h3>Consulting</h3>
  <p>Beacon Advisory has certified professional consultants to work with you to help increase the business.</p>
</div>
<div class="abs tile" style="left:401px">
  <div class="photo" role="img" aria-label="Group of staff members standing together"></div><div class="shade"></div>
  <svg class="ico" width="40" height="40" viewBox="0 0 40 40" fill="none" stroke="#fff" stroke-width="2.5"><circle cx="20" cy="20" r="16"/><circle cx="20" cy="16" r="5"/><path d="M11 30c2-6 16-6 18 0"/></svg>
  <h3>Staff Augmentation</h3>
  <p>For years Beacon Advisory as been offering our customers the ability to augment their existing staff</p>
</div>
<div class="abs tile" style="left:802px">
  <div class="photo" role="img" aria-label="Business team posing in an office"></div><div class="shade"></div>
  <svg class="ico" width="40" height="40" viewBox="0 0 40 40" fill="none" stroke="#fff" stroke-width="2.5"><circle cx="20" cy="22" r="12"/><circle cx="8" cy="8" r="4"/><circle cx="32" cy="8" r="4"/></svg>
  <h3>Offshore</h3>
  <p>Our Offshore development model has a unique distinction of providing efficient software solutions</p>
</div>

<div class="abs about-photo" role="img" aria-label="Smiling businesswoman in a dark suit with arms crossed"></div>
<h2 class="abs about-title">KNOW ABOUT US</h2>
<p class="abs about-text">Today's IT market is a dynamic, fast-paced industry, with ever-increasing demands. Meeting these demands for over 25 years, Beacon Advisory maintains a global presence, aggressively recruiting expertly qualified IT and Management Professionals from around the world and cultivating key partnerships.</p>
<div class="abs btn-solid">READ MORE</div>

<section class="abs offers"></section>
<div class="abs offer center" style="left:177px">
  <svg width="40" height="56" viewBox="0 0 40 56" fill="none" stroke="#333" stroke-width="2"><circle cx="20" cy="20" r="14" fill="#f3d65a"/><path d="M14 38h12M15 44h10M17 50h6"/></svg>
  <h4>Consulting</h4>
  <p>Beacon Advisory has certified professional consultants to work with you to help increase the business.</p>
  <a>READ MORE</a>
</div>
<div class="abs offer center" style="left:470px">
  <svg width="56" height="56" viewBox="0 0 56 56"><circle cx="28" cy="28" r="24" fill="none" stroke="#d23b2f" stroke-width="4"/><circle cx="28" cy="24" r="7" fill="#333"/><path d="M16 44c3-9 21-9 24 0z" fill="#333"/></svg>
  <h4>Staff<br>Augmentation</h4>
  <p>For years Beacon Advisory as been offering our customers the ability to augment their existing staff</p>
  <a>READ MORE</a>
</div>
<div class="abs offer center" style="left:761px">
  <svg width="56" height="56" viewBox="0 0 56 56"><circle cx="28" cy="32" r="18" fill="#3a8fd6"/><path d="M18 28c6-4 10 4 16-2 4 6-2 12-8 14z" fill="#4caf50"/><circle cx="12" cy="10" r="6" fill="#e0a030"/><circle cx="44" cy="10" r="6" fill="#e05050"/></svg>
  <h4>Offshore</h4>
  <p>Our Offshore development model has a unique distinction of providing efficient software solutions</p>
  <a>READ MORE</a>
</div>

<h2 class="abs sec-title center">OUR SERVICES</h2>
<p class="abs sec-intro center">IT includes such items as the systems software, application software, computer hardware, networks and databases associated with managing an organization's information. The chief information officer leads the department that manages most aspects of an organization's IT.</p>

<section class="abs services"></section>
<div class="abs service center" style="left:0">
  <svg width="70" height="56" viewBox="0 0 70 56" fill="#bbb"><circle cx="26" cy="30" r="16"/><circle cx="26" cy="30" r="6" fill="#efefef"/><rect x="38" y="4" width="8" height="44" transform="rotate(40 42 26)"/></svg>
  <h5>DEVELOPMENT</h5>
  <p>Drawing on our experience in all major industries, we develop solutions that meet the most challenging IT problems.</p>
</div>
<div class="abs service featured center" style="left:301px">
  <svg width="56" height="56" viewBox="0 0 56 56"><rect x="2" y="2" width="52" height="52" rx="6" fill="var(--blue)"/><circle cx="18" cy="18" r="6" fill="none" stroke="#fff" stroke-width="3"/><circle cx="38" cy="38" r="6" fill="none" stroke="#fff" stroke-width="3"/><path d="M22 22l12 12M38 12v10M12 38h10" stroke="#fff" stroke-width="3"/></svg>
  <h5>TECHNOLOGY</h5>
  <p>Beacon Advisory Training programs are perfect for individuals to enhance their careers. Our hands-on practical.</p>
</div>
<div class="abs service center" style="left:600px">
  <svg width="56" height="56" viewBox="0 0 56 56" fill="#bbb"><path d="M28 4a18 18 0 0 1 18 18c0 8-6 12-6 18v10H20V40c0-6-8-10-8-18A16 16 0 0 1 28 4z"/><circle cx="28" cy="22" r="6" fill="#efefef"/></svg>
  <h5>IT CONSULTING</h5>
  <p>Information technology should improve business results. Our team helps companies make sure it does. We look at IT issues.</p>
</div>
<div class="abs service center" style="left:900px">
  <svg width="80" height="56" viewBox="0 0 80 56" fill="#bbb"><rect x="0" y="8" width="14" height="36"/><rect x="66" y="8" width="14" height="36"/><path d="M14 14h18l8 6 8-6h18v24l-14 12-14-10-14 10-10-10z"/></svg>
  <h5>BUSINESS</h5>
  <p>Our Offshore development model has a unique distinction of providing efficient software solutions with cost and quality advantage.</p>
</div>

<section class="abs banner" role="img" aria-label="Man in glasses and light shirt working at a desk"></section>
<div class="abs banner-veil"></div>
<p class="abs banner-quote center">Effective integration of information technology into an organization's business processes has become increasingly crucial to prosperity</p>

<div class="abs news-left"></div>
<div class="abs news-right"></div>
<h2 class="abs news-title center">NEWSLATTER</h2>
<div class="abs news-input">EMAIL ID
  <span class="news-send"><svg width="20" height="20" viewBox="0 0 24 24" fill="none" stroke="#fff" stroke-width="2"><path d="M22 2L2 10l8 4 4 8z M10 14L22 2"/></svg></span>
</div>

<footer class="abs footer"></footer>
<h2 class="abs footer-title center">KEEP CONNECT WITH US</h2>
<div class="abs office" style="left:80px">
  <h6><svg width="38" height="34" viewBox="0 0 38 34" fill="none" stroke="#fff" stroke-width="2"><rect x="4" y="8" width="14" height="24"/><rect x="18" y="2" width="16" height="30"/><path d="M8 14h6M8 20h6M22 8h8M22 14h8M22 20h8M0 32h38"/></svg>Head Office</h6>
  <p>1450 Harbor Lane<br>Suite 210<br>Millbrook, NJ 07199</p>
</div>
<div class="abs divider" style="left:384px"></div>
<div class="abs office" style="left:458px">
  <h6><svg width="38" height="34" viewBox="0 0 38 34" fill="none" stroke="#fff" stroke-width="2"><circle cx="18" cy="15" r="13"/><circle cx="18" cy="15" r="5"/><path d="M10 30l8-4 8 4"/></svg>Technical Center</h6>
  <p>27100 Orchard Road<br>Suite 330<br>Lakeview Hills, MI 48999</p>
</div>
<div class="abs divider" style="left:781px"></div>
<div class="abs office" style="left:858px">
  <h6><svg width="38" height="34" viewBox="0 0 38 34" fill="none" stroke="#fff" stroke-width="2"><rect x="8" y="2" width="22" height="30"/><path d="M13 8h4M21 8h4M13 14h4M21 14h4M13 20h4M21 20h4M16 32v-6h6v6M2 32h34"/></svg>West Coast Office</h6>
  <p>4800 Summit Place<br>Suite 600<br>Bayside, CA 95999</p>
</div>

<div class="abs copyright">© <b>BEACON ADVISORY</b> · 2016. All Rights Reserved.</div>

</body>
</html>
```